The Plate Compass

Cutting Through the Noise to What Actually Works.

Nutrition book

Target Market(s)

People looking to be or get healthy and eat right.

```html
<!DOCTYPE html>
<html lang="en">
<head>
<meta charset="utf-8">
<title>The Plate Compass</title>
<link rel="stylesheet" href="https://fonts.googleapis.com/css2?family=Oswald:wght@500;600;700&family=Montserrat:wght@400;500;600&family=Roboto:wght@400&display=swap">
<style>
  :root {
    --bg-top: #122017;
    --bg-bottom: #0a120d;
    --ink-light: #f1efe8;
    --ink-dark: #1f221f;
    --accent-green: #7f8c56;
    --accent-gold: #b9a46b;
    --rule: #5f6a55;
    --tier-calories: #e7e3d8;
    --tier-protein: #687753;
    --tier-quality: #7a6a4c;
    --tier-timing: #4b6070;
    --tier-supplements: #262c27;
    --muted: #9aa39a;
  }
  * { margin: 0; padding: 0; box-sizing: border-box; }
  html, body { width: 800px; height: 1200px; overflow: hidden; }
  body {
    position: relative;
    background: radial-gradient(ellipse at 50% 40%, var(--bg-top), var(--bg-bottom) 80%);
    font-family: "Montserrat", sans-serif;
    color: var(--ink-light);
  }
  .poster { position: relative; width: 800px; height: 1200px; }
  .abs { position: absolute; }
  .center { left: 0; right: 0; text-align: center; }

  .kicker { top: 22px; font-family: "Oswald", sans-serif; font-weight: 500; font-size: 19px; letter-spacing: 3px; color: var(--accent-gold); }
  .kicker-rule { top: 33px; height: 1px; background: var(--rule); width: 150px; }
  .kicker-rule.left { left: 38px; }
  .kicker-rule.right { right: 38px; }
  .kicker-sub { top: 55px; font-family: "Oswald", sans-serif; font-weight: 500; font-size: 20px; letter-spacing: 3px; }

  .title { font-family: "Oswald", sans-serif; font-weight: 700; line-height: 1; text-transform: uppercase; letter-spacing: 2px; }
  .title-the { top: 96px; font-size: 116px; }
  .title-main { top: 207px; font-size: 116px; }
  .title-accent { top: 322px; font-size: 116px; color: var(--accent-green); }

  .divider { top: 471px; height: 1px; background: var(--rule); width: 290px; }
  .divider.left { left: 98px; }
  .divider.right { right: 98px; }
  .divider-badge { top: 457px; left: 386px; width: 28px; height: 28px; }

  .subtitle { top: 503px; font-family: "Oswald", sans-serif; font-weight: 500; font-size: 21px; letter-spacing: 2.5px; line-height: 25px; }
  .subtitle-accent { top: 558px; font-family: "Oswald", sans-serif; font-weight: 500; font-size: 18px; letter-spacing: 2px; color: var(--accent-gold); }

  .pyramid { top: 0; left: 0; }

  .tier { position: absolute; }
  .tier-name { font-family: "Oswald", sans-serif; font-weight: 600; font-size: 28px; line-height: 0.9; letter-spacing: 1px; }
  .tier-role { font-family: "Oswald", sans-serif; font-weight: 500; font-size: 13px; line-height: 15px; letter-spacing: 1.5px; margin-top: 3px; }
  .tier-note { font-family: "Roboto", sans-serif; font-size: 11px; line-height: 12.5px; margin-top: 1px; }
  .tier.light { color: var(--ink-dark); }
  .tier.light .tier-role { color: #333; }

  .noise-list { left: 696px; top: 898px; font-family: "Oswald", sans-serif; font-size: 14px; letter-spacing: 1.5px; line-height: 19px; color: var(--muted); }
  .noise-title { left: 672px; top: 1022px; font-family: "Oswald", sans-serif; font-weight: 600; font-size: 23px; color: var(--accent-green); }
  .noise-note { left: 672px; top: 1053px; font-size: 12px; line-height: 16px; color: var(--muted); }

  .footer-rule { top: 1111px; height: 1px; background: var(--rule); width: 345px; }
  .footer-rule.left { left: 40px; }
  .footer-rule.right { right: 40px; }
  .footer-leaf { top: 1101px; left: 391px; width: 18px; height: 22px; }
  .footer-line { top: 1135px; font-family: "Oswald", sans-serif; font-weight: 500; font-size: 19px; letter-spacing: 2.5px; color: var(--accent-gold); }
  .footer-tag { top: 1162px; font-family: "Oswald", sans-serif; font-weight: 500; font-size: 19px; letter-spacing: 3px; }
</style>
</head>
<body>
<main class="poster">
  <div class="abs kicker-rule left"></div>
  <div class="abs kicker-rule right"></div>
  <p class="abs center kicker">CUTTING THROUGH THE NOISE</p>
  <p class="abs center kicker-sub">TO WHAT ACTUALLY WORKS.</p>

  <h1>
    <span class="abs center title title-the">THE</span>
    <span class="abs center title title-main">PLATE</span>
    <span class="abs center title title-accent">COMPASS</span>
  </h1>

  <div class="abs divider left"></div>
  <div class="abs divider right"></div>
  <svg class="abs divider-badge" viewBox="0 0 28 28" aria-hidden="true">
    <circle cx="14" cy="14" r="12.5" fill="none" stroke="var(--accent-gold)" stroke-width="1.3"/>
    <path d="M14 20 V12 M14 14 C10 14 9 11 9 9 C12 9 14 11 14 14 M14 13 C14 10 16 8 19 8 C19 11 17 13 14 13" fill="none" stroke="var(--accent-gold)" stroke-width="1.3"/>
  </svg>

  <p class="abs center subtitle">A SIMPLE, EVIDENCE-BASED GUIDE TO<br>EATING RIGHT AND GETTING HEALTHY</p>
  <p class="abs center subtitle-accent">FOR REAL RESULTS THAT LAST.</p>

  <svg class="abs pyramid" width="800" height="1200" viewBox="0 0 800 1200" aria-hidden="true">
    <defs>
      <linearGradient id="shade" x1="0" y1="0" x2="0" y2="1">
        <stop offset="0" stop-color="#fff" stop-opacity="0.10"/>
        <stop offset="1" stop-color="#000" stop-opacity="0.22"/>
      </linearGradient>
    </defs>
    <g class="tier-shapes">
      <polygon points="228,597 535,597 545,691 218,691" fill="var(--tier-calories)"/>
      <polygon points="190,697 573,697 584,788 180,788" fill="var(--tier-protein)"/>
      <polygon points="162,792 606,792 618,879 150,879" fill="var(--tier-quality)"/>
      <polygon points="128,882 645,882 658,966 116,966" fill="var(--tier-timing)"/>
      <polygon points="84,970 686,970 700,1067 70,1067" fill="var(--tier-supplements)"/>
      <polygon points="228,597 535,597 545,691 218,691" fill="url(#shade)"/>
      <polygon points="190,697 573,697 584,788 180,788" fill="url(#shade)"/>
      <polygon points="162,792 606,792 618,879 150,879" fill="url(#shade)"/>
      <polygon points="128,882 645,882 658,966 116,966" fill="url(#shade)"/>
      <polygon points="84,970 686,970 700,1067 70,1067" fill="url(#shade)"/>
    </g>
    <g class="tier-icons">
      <path d="M268 667 C252 667 248 652 256 640 C258 648 262 649 263 646 C260 636 266 626 272 622 C272 632 286 640 284 654 C283 662 277 667 268 667 Z" fill="#1f221f"/>
      <path d="M235 765 C230 752 232 738 240 730 C246 726 252 729 252 734 C248 736 246 741 248 746 C254 742 262 744 266 750 C268 758 262 765 252 766 Z" fill="var(--ink-light)"/>
      <path d="M214 823 C206 818 196 822 196 836 C196 850 205 860 214 856 C223 860 232 850 232 836 C232 822 222 818 214 823 Z M214 822 C214 815 217 811 221 809" fill="var(--ink-light)" stroke="var(--ink-light)" stroke-width="2"/>
      <circle cx="195" cy="921" r="17" fill="none" stroke="var(--ink-light)" stroke-width="2.5"/>
      <path d="M195 909 V921 L203 927" fill="none" stroke="var(--ink-light)" stroke-width="2.5" stroke-linecap="round"/>
      <g transform="rotate(-45 146 1018)">
        <rect x="126" y="1008" width="40" height="20" rx="10" fill="none" stroke="var(--ink-light)" stroke-width="2.5"/>
        <line x1="146" y1="1008" x2="146" y2="1028" stroke="var(--ink-light)" stroke-width="2.5"/>
      </g>
    </g>
    <path d="M640 1012 C662 1008 676 994 684 966" fill="none" stroke="var(--muted)" stroke-width="1.3" stroke-dasharray="3 3"/>
    <path d="M678 970 L684 962 L689 971" fill="none" stroke="var(--muted)" stroke-width="1.3"/>
  </svg>

  <div class="tier light" style="left:318px; top:612px;">
    <h2 class="tier-name">CALORIES</h2>
    <p class="tier-role">THE FOUNDATION</p>
    <p class="tier-note">Energy balance determines<br>whether you gain, lose, or maintain.</p>
  </div>
  <div class="tier" style="left:290px; top:708px;">
    <h2 class="tier-name">PROTEIN</h2>
    <p class="tier-role">BUILD &amp; PROTECT</p>
    <p class="tier-note">The key macronutrient for muscle,<br>satiety, and metabolic health</p>
  </div>
  <div class="tier" style="left:262px; top:802px;">
    <h2 class="tier-name">FOOD QUALITY</h2>
    <p class="tier-role">NOURISH &amp; THRIVE</p>
    <p class="tier-note">Nutrient-dense foods fuel your body,<br>support health, and improve results.</p>
  </div>
  <div class="tier" style="left:236px; top:890px;">
    <h2 class="tier-name">MEAL TIMING</h2>
    <p class="tier-role">STRATEGIZE &amp; OPTIMIZE</p>
    <p class="tier-note">When you eat can support energy,<br>performance, and fat loss</p>
  </div>
  <div class="tier" style="left:200px; top:986px;">
    <h2 class="tier-name">SUPPLEMENTS</h2>
    <p class="tier-role">FILL THE GAPS</p>
    <p class="tier-note">Useful tools, not magic. They support<br>a solid foundation, not replace it.</p>
  </div>

  <p class="abs noise-list">TRENDS<br>FADS<br>DIETS<br>MYTHS<br>HYPE<br>CONFUSION</p>
  <p class="abs noise-title">NOISE</p>
  <p class="abs noise-note">Distracts and<br>Complicates</p>

  <div class="abs footer-rule left"></div>
  <div class="abs footer-rule right"></div>
  <svg class="abs footer-leaf" viewBox="0 0 18 22" aria-hidden="true">
    <path d="M9 21 C3 16 3 8 11 1 C17 8 15 16 9 21 Z M9 21 L11 6" fill="var(--accent-green)" stroke="var(--bg-bottom)" stroke-width="1"/>
  </svg>
  <p class="abs center footer-line">FOCUS ON WHAT MATTERS. DROWN OUT THE REST.</p>
  <p class="abs center footer-tag">BUILD HEALTH. BUILD RESULTS.</p>
</main>
</body>
</html>
```